Real estate broker business card

Want a modern celan but effective business card for my residential and commercial real estate business. I want the back of the card to advertise my services and to capture business. I have attached the back of my current business card fore ideas
Updates

Logos, photo and text updates added! Added Saturday, September 3, 2016

Project Deadline Extended Reason: LOGOS, PHOTOS AND TEST JUST UPLOADED! I'M READY TO PICK A DESIGN! THANK YOU! Added Saturday, September 3, 2016

Target Market(s)

home buyers and seller. commercial buyers and sellers

Industry/Entity Type

Real Estate

Contact Information for Business Card

must have my contact information and my photo

Requirements
Must have
• Carla Ventrino
• Owner & Qualifying Broker
• Ventrino Real Estate Services
• 505.718.2094
• carla@ventrinohomes.example
• www.ventrinohomes.example
Nice to have
• metallic
• Business capture text: " Don't buy or lease property without someone looking out for your best interests. I will represent you on your home or investment purchase for FREE!"
• "Home owners, call today to receive a FREE market analysis for your homes value!

```html
<!DOCTYPE html>
<html lang="en">
<head>
<meta charset="utf-8">
<title>Ventrino Real Estate Services — Business Card</title>
<link rel="stylesheet" href="https://fonts.googleapis.com/css2?family=Cinzel:wght@700&family=Montserrat:wght@400;500;600&display=swap">
<style>
  :root {
    --page-bg: #3a3b3d;
    --card-white: #ffffff;
    --card-grey: #e4e5e6;
    --teal: #1d6b7a;
    --teal-light: #2b8c9b;
    --ink: #4a4d50;
    --frame: #5b5d60;
    --photo-dark: #2f4a2c;
    --photo-mid: #6b5a4e;
  }
  * { margin: 0; padding: 0; box-sizing: border-box; }
  html, body { width: 1200px; height: 900px; overflow: hidden; }
  body {
    background: var(--page-bg);
    font-family: "Montserrat", Arial, sans-serif;
    color: var(--ink);
    position: relative;
  }
  .card {
    position: absolute;
    left: 285px;
    width: 630px;
    height: 360px;
    border-radius: 26px;
    overflow: hidden;
    box-shadow: 0 10px 30px rgba(0,0,0,.35);
  }
  .card--back { top: 70px; background: var(--card-grey); }
  .card--front { top: 470px; background: var(--card-white); }

  /* Back side */
  .portrait {
    position: absolute;
    top: 22px; right: 26px;
    width: 220px; height: 172px;
    border: 5px solid var(--frame);
    background: radial-gradient(circle at 45% 50%, var(--photo-mid) 0%, #4a3a32 35%, var(--photo-dark) 75%);
  }
  .brand {
    position: absolute;
    left: 40px; top: 196px;
    display: flex; align-items: center; gap: 12px;
    color: var(--teal);
    font-weight: 600;
  }
  .brand__mark { width: 34px; height: 34px; background: var(--teal); border-radius: 4px; }
  .brand__name { font-size: 34px; line-height: 1; letter-spacing: 1px; text-transform: uppercase; }
  .brand__sub { font-size: 11.5px; letter-spacing: 2.8px; text-transform: uppercase; margin-top: 4px; }
  .pitch {
    position: absolute;
    left: 40px; top: 262px;
    width: 440px;
    font-size: 13px;
    line-height: 1.35;
  }
  .pitch p + p { margin-top: 6px; }
  .pitch strong { color: var(--teal); font-weight: 600; }

  /* Front side */
  .front-brand {
    position: absolute;
    left: 40px; top: 0; bottom: 0; width: 250px;
    display: flex; flex-direction: column; justify-content: center; align-items: center; gap: 14px;
    color: var(--teal); font-weight: 600; text-align: center;
  }
  .front-brand__mark { width: 64px; height: 64px; background: var(--teal); border-radius: 6px; }
  .front-brand__name { font-size: 30px; letter-spacing: 2px; text-transform: uppercase; line-height: 1.1; }
  .front-brand__sub { font-size: 10.5px; letter-spacing: 2.6px; text-transform: uppercase; }
  .divider {
    position: absolute;
    left: 318px; top: 90px;
    width: 1.5px; height: 180px;
    background: var(--teal);
  }
  .contact {
    position: absolute;
    left: 350px; top: 98px;
  }
  .contact__name {
    font-family: "Cinzel", Georgia, serif;
    font-weight: 700;
    font-size: 25px;
    color: var(--teal);
    letter-spacing: .5px;
  }
  .contact__title { font-size: 14px; margin-top: 2px; }
  .contact__list { list-style: none; margin-top: 16px; font-size: 14px; }
  .contact__list li { display: flex; align-items: center; gap: 10px; margin-bottom: 5px; }
  .contact__list svg { width: 12px; height: 12px; fill: var(--teal); flex: none; }
</style>
</head>
<body>

<section class="card card--back" aria-label="Card back">
  <div class="portrait" role="img" aria-label="Portrait photo of Carla Ventrino"></div>

  <div class="brand">
    <span class="brand__mark"></span>
    <div>
      <div class="brand__name">Ventrino</div>
      <div class="brand__sub">Real Estate Services</div>
    </div>
  </div>

  <div class="pitch">
    <p>Don't buy or lease property without someone looking out for your best interests. I will represent you on your home or investment purchase for <strong>FREE</strong>!</p>
    <p>Home owners, call today to receive a <strong>FREE</strong> market analysis for your homes value!</p>
  </div>
</section>

<section class="card card--front" aria-label="Card front">
  <div class="front-brand">
    <span class="front-brand__mark"></span>
    <div class="front-brand__name">Ventrino</div>
    <div class="front-brand__sub">Real Estate Services</div>
  </div>

  <div class="divider"></div>

  <div class="contact">
    <h1 class="contact__name">CARLA VENTRINO</h1>
    <div class="contact__title">Owner &amp; Qualifying Broker</div>
    <ul class="contact__list">
      <li>
        <svg viewBox="0 0 24 24" aria-hidden="true"><path d="M6.6 10.8a15.1 15.1 0 0 0 6.6 6.6l2.2-2.2c.3-.3.7-.4 1-.2 1.1.4 2.3.6 3.6.6.6 0 1 .4 1 1V20c0 .6-.4 1-1 1C10.6 21 3 13.4 3 4c0-.6.4-1 1-1h3.5c.6 0 1 .4 1 1 0 1.3.2 2.5.6 3.6.1.3 0 .7-.2 1z"/></svg>
        505.718.2094
      </li>
      <li>
        <svg viewBox="0 0 24 24" aria-hidden="true"><path d="M2 5h20v14H2zm2 2v.5l8 5 8-5V7zm0 2.8V17h16V9.8l-8 5z"/></svg>
        carla@ventrinohomes.example
      </li>
      <li>
        <svg viewBox="0 0 24 24" aria-hidden="true"><path d="M12 2a10 10 0 1 0 0 20 10 10 0 0 0 0-20zm6.9 6h-3a15 15 0 0 0-1.3-4 8 8 0 0 1 4.3 4zM12 4c.8 1.2 1.5 2.5 1.9 4h-3.8c.4-1.5 1.1-2.8 1.9-4zM4.3 14a8 8 0 0 1 0-4h3.4a16 16 0 0 0 0 4zm.8 2h3a15 15 0 0 0 1.3 4 8 8 0 0 1-4.3-4zm3-8h-3a8 8 0 0 1 4.3-4 15 15 0 0 0-1.3 4zM12 20c-.8-1.2-1.5-2.5-1.9-4h3.8c-.4 1.5-1.1 2.8-1.9 4zm2.3-6H9.7a14 14 0 0 1 0-4h4.6a14 14 0 0 1 0 4zm.3 6a15 15 0 0 0 1.3-4h3a8 8 0 0 1-4.3 4zm1.7-6a16 16 0 0 0 0-4h3.4a8 8 0 0 1 0 4z"/></svg>
        www.ventrinohomes.example
      </li>
    </ul>
  </div>
</section>

</body>
</html>
```